Ward Compass Business Card Design*

We need a business card design for our company Ward Compass. Our company is specialized in providing online consulting services regarding medical institutions, hospitals and doctors. We work with patients worldwide looking to choose between healthcare providers. We have a website you may use as a reference, where we list doctors and clinics worldwide. So we target Medical providers as well as patients worldwide.
Target Market(s)
Medical Providers and patients around the world
Industry/Entity Type
Medical
Contact Information for Business Card
Salwa Kettani
CEO
+90 612 348 2175
info@wardcompass.example
www.wardcompass.example
14 Annakhil 7 H.R.B. Rabat, Morocco
Requirements
Must have
- Company logo/name on one full side, personal info and smaller logo and company name on the other side.
Nice to have
- Smart and elegant design

```html
<!DOCTYPE html>
<html lang="en">
<head>
<meta charset="utf-8">
<title>Ward Compass – Business Card</title>
<link rel="stylesheet" href="https://fonts.googleapis.com/css2?family=Open+Sans:wght@400;600;700&display=swap">
<style>
  :root {
    --navy: #1c3f6d;
    --slate: #7b7b7b;
    --paper: #ffffff;
    --backdrop: #2b2b2b;
    --soft-grey: #efefef;
    --white-text: #ffffff;
  }
  * { box-sizing: border-box; margin: 0; padding: 0; }
  html, body { width: 1200px; height: 768px; overflow: hidden; }
  body {
    background: var(--backdrop);
    font-family: "Open Sans", Arial, sans-serif;
    display: flex;
    flex-direction: column;
    align-items: center;
    justify-content: center;
    gap: 40px;
  }
  .card {
    width: 560px;
    height: 320px;
    position: relative;
    overflow: hidden;
    box-shadow: 0 10px 30px rgba(0,0,0,.45);
  }

  /* Back side */
  .card-back { background: var(--navy); color: var(--white-text); }
  .back-brand {
    position: absolute; left: 0; right: 0; top: 120px;
    display: flex; align-items: center; justify-content: center; gap: 12px;
  }
  .brand-dot {
    width: 22px; height: 22px; border-radius: 50%;
    background: currentColor; flex: none;
  }
  .brand-name {
    font-weight: 600; letter-spacing: .12em; text-transform: uppercase;
    font-size: 26px;
  }
  .back-web {
    position: absolute; left: 0; right: 0; bottom: 42px;
    text-align: center; font-size: 15px; letter-spacing: .32em;
  }

  /* Front side */
  .card-front { background: var(--slate); color: var(--white-text); }
  .front-field {
    position: absolute; left: 0; top: 0; width: 100%; height: 100%;
  }
  .holder { position: absolute; left: 34px; top: 34px; }
  .holder-name { font-weight: 700; font-size: 21px; line-height: 1.1; }
  .holder-role { font-size: 13px; }
  .address { position: absolute; left: 34px; top: 140px; font-size: 14px; line-height: 1.35; }
  .contacts { position: absolute; left: 34px; top: 200px; list-style: none; font-size: 14px; line-height: 1.45; }
  .contacts li { display: flex; align-items: center; gap: 9px; }
  .contacts svg { width: 13px; height: 13px; fill: var(--white-text); flex: none; }
  .front-brand {
    position: absolute; left: 330px; top: 146px;
    display: flex; align-items: center; gap: 10px; color: var(--navy);
  }
  .front-brand .brand-dot { width: 16px; height: 16px; }
  .front-brand .brand-name { font-size: 18px; }
</style>
</head>
<body>

  <section class="card card-back" aria-label="Card back">
    <div class="back-brand">
      <span class="brand-dot"></span>
      <span class="brand-name">Ward Compass</span>
    </div>
    <p class="back-web">www.wardcompass.example</p>
  </section>

  <section class="card card-front" aria-label="Card front">
    <svg class="front-field" viewBox="0 0 560 320" aria-hidden="true">
      <path d="M560 30 L360 30 A175 175 0 0 0 360 340 L560 340 Z" fill="var(--paper)"/>
      <circle cx="405" cy="185" r="110" fill="none" stroke="var(--soft-grey)" stroke-width="2"/>
    </svg>

    <div class="holder">
      <p class="holder-name">Salwa Kettani</p>
      <p class="holder-role">CEO</p>
    </div>

    <p class="address">14 Annakhil 7<br>H.R.B. Rabat, Morocco</p>

    <ul class="contacts">
      <li>
        <svg viewBox="0 0 16 16"><path d="M3 1h3l1.5 4-2 1.3a9 9 0 0 0 4.2 4.2L11 8.5l4 1.5v3a2 2 0 0 1-2 2A13 13 0 0 1 1 3a2 2 0 0 1 2-2z"/></svg>
        +90 612 348 2175
      </li>
      <li>
        <svg viewBox="0 0 16 16"><path d="M1 3h14v10H1z M1.5 3.5 8 9l6.5-5.5" stroke="#7b7b7b" stroke-width="1.2"/></svg>
        info@wardcompass.example
      </li>
      <li>
        <svg viewBox="0 0 16 16"><circle cx="8" cy="8" r="7"/><path d="M1 8h14M8 1c-3 3.5-3 10.5 0 14M8 1c3 3.5 3 10.5 0 14" stroke="#7b7b7b" stroke-width="1" fill="none"/></svg>
        www.wardcompass.example
      </li>
    </ul>

    <div class="front-brand">
      <span class="brand-dot"></span>
      <span class="brand-name">Ward Compass</span>
    </div>
  </section>

</body>
</html>
```